Visualisation Software brochure

i need a sales brochure for a new visualisation software company called Lumora Studio Max.
The software has been specifically designed for manufacturers, distributers and retailers in the design / décor / furnishing / building industries. It allows customers can then import unlimited numbers of digital photos of rooms from their own home or take advantage of a library of pre-made photos, and then render different products from your catalogue into that photo to see what the finished look will be.
i have attached:
1) a mock up of the home page of the website
2) example of brochure wording that i have put together (although i am a little unsure about what other words i can add - so any suggestions here would be good)
3) i have attached some examples of other brochures that i like and would like similar designs
I am after a classy brochure used by a large corporate technology company that is given to executives and gives an impression of quality, trustworthiness and innovation.
• the colour blue as per the colours on my website mock up provided in the design brief
• I like simple, smart, clean and uncluttered design
• I like simple, clean and uncluttered design
• I like pictures that fit in with my technology (whether that be home and interior design, mixing virtual world and real world, visualising an idea) rather than basic stock of corporate people
Updates
Target Market(s)
marketing professionals
Industry/Entity Type
Software
Font styles to use
Look and feel
Each slider illustrates characteristics of the customer's brand and the style your logo design should communicate.

```html
<!DOCTYPE html>
<html lang="en">
<head>
<meta charset="utf-8">
<title>Lumora Studio Max – Sales Brochure</title>
<link rel="stylesheet" href="https://fonts.googleapis.com/css2?family=Exo+2:wght@300;400;600;700&display=swap">
<style>
  :root {
    --blue: #2e8ff2;
    --blue-dark: #1f7fe0;
    --ink: #222;
    --body: #555;
    --paper: #ffffff;
    --backdrop: #ededed;
  }
  * { margin: 0; padding: 0; box-sizing: border-box; }
  html, body { width: 887px; height: 1200px; overflow: hidden; }
  body { background: var(--backdrop); font-family: "Exo 2", Arial, sans-serif; color: var(--ink); position: relative; }

  .page { position: absolute; background: var(--paper); overflow: hidden; }
  .page-4 { left: 54px; top: 33px; width: 395px; height: 557px; }
  .page-5 { left: 450px; top: 33px; width: 423px; height: 557px; }
  .page-6 { left: 54px; top: 603px; width: 395px; height: 555px; }
  .page-7 { left: 453px; top: 603px; width: 420px; height: 555px; }

  .photo { position: absolute; left: 0; top: 0; width: 100%; height: 203px; }
  .photo-laptop { background: linear-gradient(120deg, #cfd8d2 0%, #8fa1a6 45%, #e9ece6 100%); }
  .photo-network { background: radial-gradient(ellipse at 55% 70%, #eaf6ff 0%, #7cc3ef 40%, #2f8fd2 100%); }
  .photo-growth { height: 200px; background: linear-gradient(110deg, #56b7c9 0%, #8ccf9c 45%, #c7e08a 75%, #e4edb0 100%); }
  .photo-interior { height: 200px; background: linear-gradient(135deg, #9ea6ad 0%, #d9dde0 45%, #7f8a95 100%); }

  .notch { position: absolute; width: 0; height: 0; border-left: 9px solid transparent; border-right: 9px solid transparent; }
  .page-5 .notch { left: 189px; top: 203px; border-top: 14px solid #3a9ad8; }
  .page-6 .notch { left: 207px; top: 200px; border-top: 14px solid #7cc6a8; }

  .page-number { position: absolute; bottom: 10px; font-size: 8px; color: var(--blue); }

  /* page 4 */
  .steps-title { position: absolute; left: 95px; top: 222px; font-size: 16px; font-weight: 300; color: var(--blue); line-height: 18px; }
  .steps-grid { position: absolute; left: 95px; top: 270px; width: 269px; display: grid; grid-template-columns: 129px 130px; grid-auto-rows: 72px; gap: 8px 10px; }
  .step { background: var(--blue); color: #fff; font-size: 6.2px; line-height: 8px; text-align: center; display: flex; align-items: center; justify-content: center; padding: 0 12px; }
  .steps-close { position: absolute; left: 205px; top: 512px; font-size: 13.5px; font-weight: 300; color: var(--blue); }

  /* page 5 */
  .audience-bracket { position: absolute; left: 50px; top: 238px; width: 21px; height: 96px; border-top: 1px solid var(--blue); border-left: 1px solid var(--blue); }
  .audience-title { position: absolute; left: 71px; top: 229px; font-size: 16.5px; font-weight: 700; color: var(--blue-dark); }
  .audience-list { position: absolute; left: 71px; top: 251px; list-style: none; font-size: 12.5px; font-weight: 300; color: var(--blue); line-height: 19.8px; }
  .processes-title { position: absolute; left: 71px; top: 356px; font-size: 11.5px; font-weight: 400; line-height: 14px; text-transform: uppercase; color: var(--ink); }

  .feature { position: absolute; }
  .feature h3 { font-size: 9px; font-weight: 400; color: var(--blue); line-height: 10.5px; padding-left: 11px; position: relative; margin-bottom: 6px; }
  .feature h3::before { content: ""; position: absolute; left: 0; top: 2px; width: 7px; height: 7px; background: var(--blue); }
  .feature p { font-size: 5.6px; line-height: 7.6px; color: var(--body); font-weight: 300; margin-bottom: 6px; }
  .page-5 .feature p { padding-left: 11px; }

  .page-6 .feature h3, .page-7 .feature h3 { font-size: 11.5px; line-height: 14px; padding-left: 14px; margin-bottom: 6px; }
  .page-6 .feature h3::before, .page-7 .feature h3::before { width: 8px; height: 8px; top: 3px; }
  .page-6 .feature p, .page-7 .feature p { font-size: 4.9px; line-height: 6.6px; padding-left: 0; }
</style>
</head>
<body>

<section class="page page-4">
  <div class="photo photo-laptop" role="img" aria-label="Photo of a person at a laptop holding a payment card"></div>
  <h2 class="steps-title">Sales process<br>6 steps to success</h2>
  <div class="steps-grid">
    <div class="step">Leverage the internet and the power of word-of-mouth</div>
    <div class="step">Sales consultants qualify customer requirements</div>
    <div class="step">Increase interest / desire via the website by seeing how virtualised product placement works – so that's how my house or room will look if I buy those products</div>
    <div class="step">Trial close by sales consultant – what is required for the customer to purchase</div>
    <div class="step">Combine the virtual and real worlds during an in-store or onsite consultation – virtual walk through your products combined with physical samples</div>
    <div class="step">Full sales opportunity close and determine steps to purchase / register</div>
  </div>
  <p class="steps-close">It all leads to the register</p>
  <span class="page-number" style="left:30px">4</span>
</section>

<section class="page page-5">
  <div class="photo photo-network" role="img" aria-label="Photo of a hand holding a tablet beneath a glowing network of connected people"></div>
  <span class="notch"></span>
  <div class="audience-bracket"></div>
  <h2 class="audience-title">Who can use Lumora Studio Max?</h2>
  <ul class="audience-list">
    <li>Consumers / general public</li>
    <li>In-store and mobile sales consultants</li>
    <li>Interior designers / decorators</li>
    <li>Professional trades</li>
  </ul>
  <h3 class="processes-title">Lumora Studio Max<br>supports the following retail processes:</h3>

  <div class="feature" style="left:60px; top:397px; width:205px">
    <h3>Customer DIY</h3>
    <p>Preparation, planning and purchasing all completed by the consumer without assistance and all from the comfort of their own homes.</p>
  </div>
  <div class="feature" style="left:60px; top:460px; width:205px">
    <h3>Sale rep consultation / qualification</h3>
    <p>Preparation and planning completed by the consumer with the assistance of a designer/sales person using the same online tool delivered via kiosks / tablets within your retail space as well as when salespeople visit customers' homes.</p>
  </div>
  <div class="feature" style="left:268px; top:397px; width:142px">
    <h3>Get the expert help of Lumora Studio Max Solutions</h3>
    <p>Preparation and planning completed for the consumer by an expert designer/sales person using the same online tool. This professional masking or detailing service can be performed by your mobile salespeople, or by people located at the retail store or by our experts in real time or as a delayed service.</p>
  </div>
  <span class="page-number" style="left:27px">5</span>
</section>

<section class="page page-6">
  <div class="photo photo-growth" role="img" aria-label="Soft green and teal image with a rising line chart arrow"></div>
  <span class="notch"></span>

  <div class="feature" style="left:38px; top:244px; width:155px">
    <h3>Advanced features for sales maximisation</h3>
    <p>Lumora Studio Max is fully customisable. We give you every opportunity to let your company's personality shine, with complete control over layout and colour schemes so the tool matches your brand.</p>
    <p>We also give you full flexibility to adapt the product catalogue to your needs, from naming conventions and descriptions to product images that showcase your range to its full potential.</p>
    <p>A leading feature caters for every retail situation: one catalogue shared across a whole store network, or separate catalogues for each individually owned and operated outlet within a franchise arrangement.</p>
  </div>
  <div class="feature" style="left:208px; top:244px; width:160px">
    <h3>Free, value-adding reports</h3>
    <p>We provide an entire suite of management reports, covering the collection and presentation of key information that will assist in sales and marketing decisions.</p>
    <p>With a handy set of analytics you can measure trends and consumer reach, capture lead data and discover your most popular products and seasonal patterns. You can also see average session lengths, projects saved and social shares. All of this is available in monthly reports so you know you are heading towards a very pretty sales picture.</p>
  </div>
  <div class="feature" style="left:208px; top:415px; width:160px">
    <h3>Available to new and old technology</h3>
    <p>Unlike other software, Lumora Studio Max is fully web standards compatible, so the entire platform works on nearly all laptops, PCs and tablets made in recent years. We have also developed three versions of the tool: one embedded on your website as a frame or separate page, one downloaded from the leading app store for phones and tablets, and one for every other mobile device.</p>
  </div>
  <span class="page-number" style="left:30px">6</span>
</section>

<section class="page page-7">
  <div class="photo photo-interior" role="img" aria-label="Photo of hands holding a tablet showing a modern dining room"></div>

  <div class="feature" style="left:22px; top:244px; width:152px">
    <h3>Customers are able to share with family and friends etc</h3>
    <p>Social media is recognised as the largest growth area for online transactions and consumer purchase decisions, followed by an increasing trend for shoppers to also visit in store. The right technology will play a huge role in product awareness, branding, business development and lead gathering.</p>
    <p>Having your virtual designer embedded on your website and apps allows customers to contribute to your digital buzz by sharing their projects on their favourite social networks. Shoppers can also save, print and email their designed scenes with your logo and company details included on every one.</p>
  </div>
  <div class="feature" style="left:190px; top:244px; width:160px">
    <h3>Unique flexibility in bringing it all together</h3>
    <p>After your customers upload their own photo, revolutionise your levels of service by offering them a real time or delayed professional masking service, so all they need to do is start applying your products to their image.</p>
    <p>Have their room scene photos detailed by your staff in real time while a salesperson sits in front of your customer, done by another location, or delay the service and email the customer a link. Alternatively our experts can provide this service as well.</p>
  </div>
  <div class="feature" style="left:190px; top:415px; width:160px">
    <h3>Use customers own room scenes</h3>
    <p>This is our most coveted service: your shoppers will have the ability to upload their own photo, outline the product areas and start applying your products immediately using our highly sophisticated rendering tool that takes your products to the next level in visualisation.</p>
  </div>
  <span class="page-number" style="left:26px">7</span>
</section>

</body>
</html>
```